20 year old business card needs re-design

We need to redesign our corporate business card look. We need something that appears more modern, eye catchy but professional.

Target Market(s)

manufacturing industry

Industry/Entity Type

Manufacturer

Contact Information for Business Card

One side can have the logo. Other side can have contact information.

Font styles to use
Serif

Colors
3277b5
33b8a4
ffffff

Requirements
Must have
• Eye catchy - need to standout from the crowd. company logo cannot change. Full name, job title, phone number and email address.
Should not have
• Fax, business address is not necessary.

```html
<!DOCTYPE html>
<html lang="en">
<head>
<meta charset="utf-8">
<title>Norvale Industrial – Business Card</title>
<link href="https://fonts.googleapis.com/css2?family=Oswald:wght@500&family=Roboto:wght@300;400;500&display=swap" rel="stylesheet">
<style>
  :root {
    --blue: #3277b5;
    --teal: #33b8a4;
    --teal-deep: #14ad98;
    --white: #ffffff;
    --ink: #2f3338;
    --muted: #5a5f66;
    --backdrop: #1c1c1e;
  }
  * { box-sizing: border-box; margin: 0; padding: 0; }
  html, body {
    width: 1200px; height: 963px; overflow: hidden;
    background: var(--backdrop);
  }
  .canvas {
    width: 1200px; height: 963px;
    display: flex; flex-direction: column;
    align-items: center; justify-content: center; gap: 56px;
  }
  .card {
    width: 640px; height: 366px;
    border-radius: 22px;
    position: relative; overflow: hidden;
  }
  /* Contact side */
  .card--front { background: var(--white); }
  .card--front .edge {
    position: absolute; left: 0; right: 0; bottom: 0; height: 9px;
    display: flex;
  }
  .edge .edge-blue { width: 36%; background: var(--blue); }
  .edge .edge-teal { flex: 1; background: var(--teal); }
  .identity {
    position: absolute; left: 118px; top: 140px; text-align: right; width: 196px;
  }
  .person-name {
    font-family: "Oswald", sans-serif; font-weight: 500;
    font-size: 31px; letter-spacing: 0.5px; line-height: 1.05;
    color: var(--teal); text-transform: uppercase;
  }
  .person-title {
    font-family: "Roboto", sans-serif; font-weight: 400;
    font-size: 15px; color: var(--ink); margin-top: 4px;
  }
  .divider {
    position: absolute; left: 332px; top: 132px; width: 2px; height: 84px;
    background: var(--blue);
  }
  .contacts {
    position: absolute; left: 352px; top: 138px;
    list-style: none;
    font-family: "Roboto", sans-serif; font-weight: 400;
    font-size: 14px; color: var(--muted);
  }
  .contacts li { display: flex; align-items: center; gap: 9px; height: 24px; }
  .contacts svg { width: 13px; height: 13px; flex: none; }
  /* Logo side */
  .card--back {
    background: linear-gradient(160deg, var(--teal) 0%, var(--teal-deep) 100%);
    display: flex; flex-direction: column; align-items: center; justify-content: center;
  }
  .brand {
    display: flex; align-items: center; gap: 14px;
    font-family: "Roboto", sans-serif; font-weight: 500;
    font-size: 46px; color: var(--white); letter-spacing: 0.5px;
  }
  .brand-mark { width: 20px; height: 20px; background: var(--white); }
  .site {
    margin-top: 46px;
    font-family: "Roboto", sans-serif; font-weight: 400;
    font-size: 16px; letter-spacing: 2px; color: var(--white);
  }
</style>
</head>
<body>
<main class="canvas">
  <section class="card card--front" aria-label="Contact side">
    <div class="identity">
      <h1 class="person-name">Dana Corvell</h1>
      <p class="person-title">Senior Project Manager</p>
    </div>
    <div class="divider"></div>
    <ul class="contacts">
      <li>
        <svg viewBox="0 0 14 14" aria-hidden="true"><rect x="3.5" y="1" width="7" height="12" rx="1.2" fill="none" stroke="var(--blue)" stroke-width="1.4"/><circle cx="7" cy="11" r="0.8" fill="var(--blue)"/></svg>
        555-014-2200 xt 118
      </li>
      <li>
        <svg viewBox="0 0 14 14" aria-hidden="true"><rect x="1" y="3" width="12" height="8.5" rx="1" fill="var(--blue)"/><path d="M1.5 3.5 L7 8 L12.5 3.5" fill="none" stroke="var(--white)" stroke-width="1.2"/></svg>
        dana@norvaleindustrial.com
      </li>
      <li>
        <svg viewBox="0 0 14 14" aria-hidden="true"><circle cx="6" cy="6" r="4" fill="none" stroke="var(--blue)" stroke-width="1.8"/><path d="M9 9 L12.5 12.5" stroke="var(--blue)" stroke-width="2" stroke-linecap="round"/></svg>
        NorvaleIndustrial.com
      </li>
    </ul>
    <div class="edge"><span class="edge-blue"></span><span class="edge-teal"></span></div>
  </section>

  <section class="card card--back" aria-label="Logo side">
    <div class="brand"><span class="brand-mark"></span>Norvale Industrial</div>
    <p class="site">norvaleindustrial.com</p>
  </section>
</main>
</body>
</html>
```